Redesign Fitness Photos for Facebook Ads Needed

We are a fun, energetic, group fitness facility that needs to have a few (3) photos doctored up and turned into ads for Facebook & Instagram.
I would like the photos to be doctored up so that they are clear, bright, energetic.  Feel free to manipulate the photos, backgrounds, cropping, cutting as needed.
I would like to include text on photos:
Pulsora
New Year
Challenge
* Fitness Training  * Nutritional Support * Motivation & Support
Join Now
The text should be roughly the size of the examples included in order to comply with facebooks text size requirements
I have included 3 examples of another gyms ads which I like how the images are eye catching and text is clearly visible and pops with color.
Although I have attached multiple images that can be used,  I am only looking for 3 completed designs to be used for ads.

You choose the images that you feel you can modify the best.
I look forward to seeing your design.
Thank you.

```html
<!DOCTYPE html>
<html lang="en">
<head>
<meta charset="utf-8">
<title>Pulsora – New Year Challenge Ad</title>
<link href="https://fonts.googleapis.com/css2?family=Barlow+Condensed:ital,wght@0,600;0,700;1,700;1,800;1,900&display=swap" rel="stylesheet">
<style>
  :root {
    --page-bg: #f1f1f1;
    --brand-blue: #1a9cf0;
    --brand-blue-deep: #0f86e0;
    --title-blue: #1b8ff0;
    --white: #ffffff;
    --ink-dark: #2b2a2c;
    --photo-violet: #5a4fb8;
    --photo-red: #c42a44;
    --photo-warm: #b98a5e;
    --photo-olive: #6d6a3a;
    --photo-shadow: #1e1a24;
  }
  * { margin: 0; padding: 0; box-sizing: border-box; }
  html, body {
    width: 1200px;
    height: 2267px;
    overflow: hidden;
    background: var(--page-bg);
    font-family: "Barlow Condensed", sans-serif;
  }
  .ad {
    position: absolute;
    left: 100px;
    top: 633px;
    width: 1000px;
    height: 1000px;
    overflow: hidden;
    background: var(--ink-dark);
    box-shadow: 0 10px 30px rgba(0,0,0,0.15);
  }
  .ad__photo {
    position: absolute;
    inset: 0 0 286px 0;
    background:
      linear-gradient(180deg, rgba(30,26,36,0) 55%, rgba(30,26,36,0.75) 100%),
      radial-gradient(ellipse 30% 22% at 82% 62%, rgba(214,170,40,0.75), rgba(214,170,40,0) 100%),
      radial-gradient(ellipse 22% 20% at 18% 55%, rgba(109,106,58,0.8), rgba(109,106,58,0) 100%),
      radial-gradient(ellipse 60% 40% at 50% 45%, rgba(185,138,94,0.55), rgba(185,138,94,0) 100%),
      radial-gradient(ellipse 35% 30% at 20% 10%, rgba(110,120,255,0.8), rgba(110,120,255,0) 100%),
      radial-gradient(ellipse 35% 30% at 88% 8%, rgba(230,40,70,0.85), rgba(230,40,70,0) 100%),
      linear-gradient(100deg, var(--photo-violet) 0%, #7a5fa8 40%, #8a4470 65%, var(--photo-red) 100%);
  }
  .ad__headline {
    position: absolute;
    left: 0;
    width: 100%;
    text-align: center;
    font-style: italic;
    text-transform: uppercase;
    line-height: 1;
    z-index: 2;
  }
  .ad__headline--small {
    top: 486px;
    font-size: 80px;
    font-weight: 800;
    color: var(--white);
    padding-left: 40px;
    text-shadow: 0 3px 8px rgba(0,0,0,0.45);
  }
  .ad__headline--big {
    top: 542px;
    font-size: 196px;
    font-weight: 900;
    color: var(--title-blue);
    letter-spacing: 1px;
    padding-left: 30px;
    text-shadow: 0 4px 10px rgba(0,0,0,0.4);
  }
  .ad__speedlines {
    position: absolute;
    left: 320px;
    top: 490px;
    z-index: 2;
  }
  .ad__band {
    position: absolute;
    left: 0;
    top: 714px;
    width: 100%;
    height: 226px;
    z-index: 1;
    background: linear-gradient(110deg, var(--brand-blue) 0%, #23a6f4 50%, var(--brand-blue-deep) 100%);
  }
  .ad__features {
    position: absolute;
    left: 100px;
    top: 36px;
    list-style: none;
    color: var(--white);
    font-style: italic;
    font-weight: 800;
    font-size: 48px;
    line-height: 58px;
    text-transform: uppercase;
  }
  .ad__rule {
    position: absolute;
    left: 50px;
    top: 212px;
  }
  .ad__brand {
    position: absolute;
    left: 620px;
    top: 50px;
    width: 320px;
    text-align: center;
    color: var(--white);
  }
  .ad__brand-name {
    font-size: 78px;
    font-weight: 700;
    line-height: 1;
    letter-spacing: 1px;
  }
  .ad__brand-tagline {
    font-size: 20px;
    font-weight: 600;
    letter-spacing: 4px;
    margin-top: 4px;
  }
  .ad__cta {
    position: absolute;
    left: 630px;
    top: 903px;
    width: 290px;
    height: 68px;
    z-index: 3;
    border-radius: 34px;
    background: var(--white);
    border: 4px solid #d9e9f5;
    color: var(--title-blue);
    font-style: italic;
    font-weight: 900;
    font-size: 42px;
    text-transform: uppercase;
    display: flex;
    align-items: center;
    justify-content: center;
    letter-spacing: 1px;
  }
</style>
</head>
<body>
  <div class="ad">
    <div class="ad__photo" role="img" aria-label="Group photo of smiling gym members flexing their arms in a studio lit with purple and red lights"></div>

    <svg class="ad__speedlines" width="420" height="60" viewBox="0 0 420 60" aria-hidden="true">
      <g stroke="#ffffff" stroke-width="2" opacity="0.8">
        <line x1="0" y1="44" x2="30" y2="44"/>
        <line x1="340" y1="40" x2="420" y2="26"/>
        <line x1="350" y1="30" x2="380" y2="12"/>
      </g>
    </svg>

    <h2 class="ad__headline ad__headline--small">New Year</h2>
    <h1 class="ad__headline ad__headline--big">Challenge</h1>

    <div class="ad__band">
      <ul class="ad__features">
        <li>Fitness Training</li>
        <li>Motivation &amp; Support</li>
        <li>Nutritional Support</li>
      </ul>

      <svg class="ad__rule" width="530" height="28" viewBox="0 0 530 28" aria-hidden="true">
        <g fill="#ffffff">
          <rect x="0" y="9" width="4" height="10"/>
          <rect x="8" y="4" width="5" height="20"/>
          <rect x="17" y="0" width="6" height="28"/>
          <rect x="23" y="12" width="484" height="4"/>
          <rect x="507" y="0" width="6" height="28"/>
          <rect x="517" y="4" width="5" height="20"/>
          <rect x="526" y="9" width="4" height="10"/>
        </g>
      </svg>

      <div class="ad__brand">
        <div class="ad__brand-name">Pulsora</div>
        <div class="ad__brand-tagline">Personal Group Training</div>
      </div>
    </div>

    <div class="ad__cta">Join Now</div>
  </div>
</body>
</html>
```